Need CATCHY/VIVID Banner design for my new UTV/ATV/Off Road Vehicle turn signal/lighting company

I need a banner ad designed so I can advertise on several different ATV (all terrain vehicle), UTV (Utility Vehicles), Golf Cart and Off-Road Vehicle forums. Ads need to be very catchy and produce a call to action. Action is getting hits to my website. Our main business is selling turn signal kits to make your side by side or your ATV/UTV street legal, as some states now allow you to drive these on public roads if you have the following items: Turn Signals, Horn, Lighted license plate bracket, headlights and brake lights. We sell all of these items for just about any model vehicle out there. Our call to action for this banner would be to get more website visits.

Target Market(s)

Off-road/outdoor enthusiasts,

Industry/Entity Type

Car Accessorie

Font styles to use
Sans Serif

Requirements
Must have
• Ad size need to be either 728x90 or 300x250. Colorful ad with an off-road vehicle integrated to the design (think UTV, side-by-side, etc.
Nice to have
• Nice to haves would be anything that makes this banner ad stand out on very boring web pages.
Should not have
• anything dull

```html
<!DOCTYPE html>
<html lang="en">
<head>
<meta charset="utf-8">
<title>ATV &amp; UTV Signal Kits Banner</title>
<link rel="stylesheet" href="https://fonts.googleapis.com/css2?family=Archivo:wght@400;700;800;900&display=swap">
<style>
  :root {
    --black: #0b0b0b;
    --red: #e01b22;
    --red-deep: #8e0f14;
    --red-mid: #c0161c;
    --yellow: #fdbb12;
    --yellow-bright: #ffc61a;
    --white: #ffffff;
    --grey-dark: #2a2a2a;
  }
  * { margin: 0; padding: 0; box-sizing: border-box; }
  html, body { width: 1200px; height: 148px; overflow: hidden; background: var(--white); }
  .banner {
    position: relative;
    width: 1200px;
    height: 148px;
    overflow: hidden;
    font-family: "Archivo", Arial, sans-serif;
    background: linear-gradient(90deg, var(--red-deep) 0%, var(--red-mid) 30%, var(--red) 50%, var(--red-deep) 72%, var(--black) 84%, var(--black) 88%, var(--yellow) 100%);
  }
  .backdrop { position: absolute; inset: 0; }
  .brand {
    position: absolute;
    left: 28px;
    top: 0;
    width: 220px;
    height: 148px;
  }
  .brand-name {
    position: absolute;
    left: 20px;
    top: 26px;
    display: flex;
    align-items: center;
    gap: 10px;
    color: var(--red);
    font-weight: 900;
    font-size: 40px;
    letter-spacing: 1px;
    line-height: 1;
  }
  .brand-mark {
    width: 18px;
    height: 18px;
    background: var(--yellow);
  }
  .brand-tagline {
    position: absolute;
    left: 0;
    top: 89px;
    color: var(--white);
    font-weight: 800;
    text-transform: uppercase;
    line-height: 1;
  }
  .brand-tagline .primary { display: block; font-size: 19px; letter-spacing: 0.1px; }
  .brand-tagline .secondary { display: block; font-size: 12.5px; margin-top: 5px; letter-spacing: 0.2px; }
  .vehicle {
    position: absolute;
    border-radius: 18px 18px 6px 6px;
  }
  .vehicle-sport {
    left: 326px;
    top: 14px;
    width: 170px;
    height: 128px;
    background: radial-gradient(ellipse at 50% 40%, #c9c5c0 0%, #7a7470 45%, #1e1e1e 100%);
  }
  .vehicle-utility {
    left: 906px;
    top: 6px;
    width: 194px;
    height: 140px;
    background: radial-gradient(ellipse at 50% 40%, #5a5a5a 0%, #2b2b2b 55%, #0d0d0d 100%);
  }
  .headline {
    position: absolute;
    left: 512px;
    top: 26px;
    text-transform: uppercase;
    line-height: 1;
  }
  .headline .title {
    display: block;
    color: var(--white);
    font-weight: 800;
    font-size: 32px;
    letter-spacing: 0.3px;
  }
  .headline .subtitle {
    display: block;
    margin-top: 8px;
    color: var(--yellow);
    font-weight: 400;
    font-size: 27px;
    letter-spacing: 0.4px;
  }
  .cta {
    position: absolute;
    left: 520px;
    top: 96px;
    width: 146px;
    height: 34px;
    display: flex;
    align-items: center;
    justify-content: center;
    background: var(--red);
    color: var(--white);
    font-weight: 800;
    font-size: 13.5px;
    letter-spacing: 0.6px;
    text-decoration: none;
    text-transform: uppercase;
  }
</style>
</head>
<body>
  <div class="banner">
    <svg class="backdrop" width="1200" height="148" viewBox="0 0 1200 148" role="img" aria-label="Red-toned mountain landscape behind the headline">
      <polygon points="0,0 300,0 300,148 0,148" fill="var(--black)"/>
      <polygon points="230,0 300,0 380,74 300,148 230,148 310,74" fill="var(--black)"/>
      <polygon points="248,0 268,0 330,56 318,66" fill="var(--red)"/>
      <polygon points="270,0 340,0 420,74 340,148 270,148 350,74" fill="var(--yellow)"/>
      <polygon points="300,40 350,74 300,108" fill="var(--yellow)"/>
      <polygon points="1105,18 1200,18 1200,42 1130,42" fill="var(--black)"/>
      <polygon points="1130,62 1200,62 1200,86 1130,86" fill="var(--black)"/>
      <polygon points="1130,106 1200,106 1200,130 1105,130" fill="var(--black)"/>
    </svg>

    <div class="brand">
      <div class="brand-name"><span class="brand-mark"></span>KIVO</div>
      <div class="brand-tagline">
        <span class="primary">Turn Signal Kits</span>
        <span class="secondary">&amp; Lighting Accessories</span>
      </div>
    </div>

    <div class="vehicle vehicle-sport" role="img" aria-label="Grey and red sport side-by-side off-road vehicle"></div>

    <div class="headline">
      <span class="title">ATV &amp; UTV Vechicle</span>
      <span class="subtitle">Signal Kits and Lighting</span>
    </div>
    <a class="cta" href="#">Click Here</a>

    <div class="vehicle vehicle-utility" role="img" aria-label="Black utility side-by-side vehicle with cargo bed"></div>
  </div>
</body>
</html>
```